Covid 19 Exit Strategy one page brochure

I would like to design, and will need URGENT help, a brochure detailing a Covid 19 Exit Strategy plan. This brochure will need to be understood easily and the graphics inside should make it easy for people to understand without reading the entire text. This project is quite urgent and needs to be completed THIS WEEK - by Saturday may 16th at the latest. I am attaching two examples. I will provide the text.

```html
<!DOCTYPE html>
<html lang="en">
<head>
<meta charset="utf-8">
<title>Covid-19 Phased Exit Strategy Brochure</title>
<link rel="stylesheet" href="https://fonts.googleapis.com/css2?family=Oswald:wght@500;600;700&family=Roboto:wght@400;700;900&family=Open+Sans:wght@400;600;700&display=swap">
<style>
  :root {
    --stage-bg: #3a3a3c;
    --paper: #f4f4f5;
    --paper-shade: #dcdcde;
    --red: #c4161c;
    --red-dark: #8f0d12;
    --ink: #1a1a1a;
    --body-text: #2a2a2a;
    --black: #111111;
    --rule: #9a9a9a;
    --white: #ffffff;
  }
  * { box-sizing: border-box; margin: 0; padding: 0; }
  html, body { width: 1200px; height: 900px; overflow: hidden; }
  body { background: var(--stage-bg); font-family: "Open Sans", Arial, sans-serif; }

  .brochure {
    position: absolute; left: 305px; top: 20px;
    width: 590px; height: 860px;
    background: linear-gradient(160deg, var(--white) 0%, var(--paper) 45%, var(--paper-shade) 100%);
    overflow: hidden;
  }
  .brochure__accent { position: absolute; inset: 0; width: 590px; height: 860px; }

  .hero-photo {
    position: absolute; left: 36px; top: 65px; width: 192px; height: 192px;
    border-radius: 50%;
    border: 6px solid var(--white);
    box-shadow: 0 0 0 6px var(--red);
    background: radial-gradient(circle at 50% 40%, #cfe3ea 0%, #7fa4b0 45%, #2f5a4e 100%);
  }

  .masthead { position: absolute; left: 250px; top: 22px; width: 330px; text-align: center; }
  .masthead__title { font-family: "Roboto", Arial, sans-serif; font-weight: 900; font-size: 38px; line-height: 1; color: var(--black); }
  .masthead__subtitle { font-family: "Roboto", Arial, sans-serif; font-weight: 700; font-size: 15px; color: var(--black); margin-top: 3px; letter-spacing: .3px; }
  .masthead__rule { border-top: 2px dotted var(--red); margin: 5px 0 4px 18px; }
  .masthead__credit { font-family: "Oswald", Arial, sans-serif; font-weight: 700; font-size: 22px; line-height: 1.15; color: var(--black); letter-spacing: .3px; }
  .masthead__credit span { color: var(--red); }

  .intro {
    position: absolute; left: 261px; top: 140px; width: 318px;
    font-size: 8.3px; line-height: 1.38; color: var(--body-text); text-align: justify;
  }

  .section-bar {
    position: absolute; font-family: "Oswald", Arial, sans-serif; font-weight: 600;
    color: var(--white); text-align: center; letter-spacing: .3px;
  }
  .section-bar--requirements {
    left: 171px; top: 254px; width: 350px; height: 25px; font-size: 17px; line-height: 25px;
    background: linear-gradient(90deg, rgba(17,17,17,0) 0%, var(--black) 12%, var(--black) 80%, rgba(17,17,17,0) 100%);
  }
  .section-bar--plan {
    left: 42px; top: 436px; width: 506px; height: 27px; font-size: 16px; line-height: 27px;
    background: linear-gradient(90deg, rgba(196,22,28,0) 0%, var(--red) 10%, var(--red) 85%, rgba(196,22,28,0) 100%);
  }

  .requirements { position: absolute; list-style: none; font-size: 7.9px; line-height: 1.32; color: var(--body-text); }
  .requirements--left { left: 25px; top: 291px; width: 220px; }
  .requirements--right { left: 323px; top: 291px; width: 244px; }
  .requirements li { position: relative; padding-left: 13px; margin-bottom: 5px; }
  .requirements li::before {
    content: ""; position: absolute; left: 0; top: 2px; width: 7px; height: 7px;
    border-radius: 50%; background: var(--red);
  }

  .stages-label {
    position: absolute; left: 0; top: 492px; width: 47px; height: 228px;
    background: var(--black); color: var(--white);
    font-family: "Oswald", Arial, sans-serif; font-weight: 600; font-size: 17px; letter-spacing: 9px;
    writing-mode: vertical-rl; transform: rotate(180deg);
    display: flex; align-items: center; justify-content: center;
  }
  .stage-tree { position: absolute; left: 0; top: 0; width: 590px; height: 860px; pointer-events: none; }

  .stage { position: absolute; left: 98px; width: 478px; }
  .stage--one { top: 483px; }
  .stage--two { top: 561px; }
  .stage--three { top: 682px; }
  .stage__entry { font-size: 7.9px; font-weight: 700; line-height: 1.3; color: var(--ink); }
  .stage__measures { display: flex; margin-top: 10px; font-size: 7.7px; line-height: 1.35; color: var(--body-text); }
  .stage__measure { padding: 0 8px; }
  .stage__measure + .stage__measure { border-left: 1px solid var(--rule); }
  .stage__measure:first-child { width: 158px; padding-left: 0; text-align: justify; }
  .stage__measure:nth-child(2) { width: 166px; }
  .stage__measure:nth-child(3) { width: 154px; }

  .footer-band { position: absolute; left: 0; top: 773px; width: 590px; height: 51px; display: flex; }
  .footer-band__call {
    width: 272px; background: var(--red); color: var(--white);
    font-family: "Oswald", Arial, sans-serif; font-weight: 600; font-size: 19px;
    display: flex; align-items: center; justify-content: center;
  }
  .footer-band__motto {
    flex: 1; background: var(--black); color: var(--white);
    font-family: "Roboto", Arial, sans-serif; font-weight: 700; font-size: 17px;
    display: flex; align-items: center; padding-left: 12px; gap: 8px;
  }
  .footer-band__motto svg { width: 42px; height: 36px; margin-top: -10px; }
</style>
</head>
<body>
  <main class="brochure">
    <svg class="brochure__accent" viewBox="0 0 590 860" aria-hidden="true">
      <polygon points="0,0 272,0 0,296" fill="var(--red)"/>
      <polygon points="272,0 290,0 0,316 0,296" fill="var(--white)"/>
      <polygon points="0,470 590,410 590,560 0,620" fill="var(--red)" opacity="0.06"/>
    </svg>

    <div class="hero-photo" role="img" aria-label="Photo of a healthcare worker wearing a face shield and surgical mask in a hospital"></div>

    <header class="masthead">
      <h1 class="masthead__title">COVID-19</h1>
      <p class="masthead__subtitle">PHASED EXIT STRATEGY</p>
      <div class="masthead__rule"></div>
      <p class="masthead__credit">DEVELOPED BY <span>ARVELLO</span></p>
      <div class="masthead__rule"></div>
    </header>

    <p class="intro">Pandemics have, historically, seen their end both medically - via herd immunity or immunizations. And while there are several clinical trials underway for potential Covid-19 vaccines, we are still a long way from deploying an effective vaccine and one that will stand the test of time as the virus changes. Covid-19 pandemic will be considered 'ended' when there are only occasional traces of localized cases that are quickly contained in specific locations. Today and in the absence of an effective vaccine(s) and for the re-opening of the economies and social activities to be successful, it is critical that the following basic conditions be in place before any lockdowns are lifted and before social activities resume:</p>

    <h2 class="section-bar section-bar--requirements">GENERAL REQUIREMENTS</h2>

    <ul class="requirements requirements--left">
      <li>Single digit downward trend of documented cases within the past 14-days.</li>
      <li>Hospitals and the health care system are capable of treating patients without operating on a crisis mode.</li>
      <li>Ability to screen and test symptomatic individuals within 24 hours of identification. Increased and sufficient testing capacity, to test at least 50% of all population if necessary within a timeframe of 3 months.</li>
      <li>Ability to surge ICU capacity on a short notice - 24h.</li>
      <li>Ability to track and trace infected patients and contacts on a live basis and across the country and ability to react quickly to any unusual trends or outbreaks.</li>
    </ul>
    <ul class="requirements requirements--right">
      <li>Plan in place to trigger targeted or full-scale containment in case of sudden outbreaks</li>
      <li>Mandatory use of masks (at least surgical grade) for everyone in all public areas and at work. Mandatory use of N95, or equivalent, masks for all healthcare front workers and for all government agencies and authorities that are involved in overseeing the containment activities.</li>
      <li>Mandatory daily checks of body temperature for everyone at the workplace or entering public areas.</li>
      <li>Mandatory sanitation in all places - use of disinfection available on a large scale</li>
    </ul>

    <h2 class="section-bar section-bar--plan">PHASED COVID-19 LOCKDOWN EXIT STRATEGY PLAN</h2>

    <div class="stages-label">STAGES</div>

    <svg class="stage-tree" viewBox="0 0 590 860" aria-hidden="true">
      <g stroke="var(--red)" stroke-width="1.5" fill="none">
        <path d="M59 496 V705"/>
        <path d="M59 496 H66"/><path d="M59 589 H66"/><path d="M59 705 H66"/>
      </g>
      <g fill="var(--red-dark)" stroke="var(--white)" stroke-width="2">
        <circle cx="79" cy="496" r="12"/><circle cx="79" cy="589" r="12"/><circle cx="79" cy="705" r="12"/>
      </g>
      <g fill="var(--white)" font-family="Roboto, Arial, sans-serif" font-weight="700" font-size="13" text-anchor="middle">
        <text x="79" y="501">1</text><text x="79" y="594">2</text><text x="79" y="710">3</text>
      </g>
    </svg>

    <section class="stage stage--one">
      <p class="stage__entry">To enter this stage, additional to the general requirements, the Effective Reproduction Number (Rt) must be less than 1 and the death rate at lessthan 3%.</p>
      <div class="stage__measures">
        <p class="stage__measure">Elderly (60+ years old) and vulnerable individuals should continue to self-isolate.</p>
        <p class="stage__measure">No more than 5 people maximum gathering at a time in public areas and at work.</p>
        <p class="stage__measure">Work from home should continue whenever and as much as possible.</p>
      </div>
    </section>

    <section class="stage stage--two">
      <p class="stage__entry">To enter stage 2 of the Covid-19 Exit Strategy, compliance to the general requirements is compulsory, additional to a successful Stage 1 outcome. The Effective Reproduction Number (Rt) for Stage 2 must be less than 0.5 and the death rate stabilized at less than 1.5%.</p>
      <div class="stage__measures">
        <p class="stage__measure">Elderly (60+ years old) and vulnerable individuals should continue to self-isolate as much as possible.</p>
        <p class="stage__measure">No more than 10 people maximum gathering at a time in public areas and at work.</p>
        <p class="stage__measure">Work from home should if possible or for jobs that do not have to be necessarily in an office setup.</p>
      </div>
    </section>

    <section class="stage stage--three">
      <p class="stage__entry">To enter stage 3 of the Covid-19 Exit Strategy, compliance to the general requirements is compulsory, additional to a successful Stage 2 outcome. The Effective Reproduction Number (Rt) for Stage 3 must be less than 0.3 and the death rate stabilized at less than 1%</p>
      <div class="stage__measures">
        <p class="stage__measure">Elderly (60+ years old) and vulnerable individuals may resume all previously exercised activities without restrictions.</p>
        <p class="stage__measure">Restrictions as to the number of people gathering together can be lifted. Social distancing can be relaxed. However, wear of masks may continue</p>
        <p class="stage__measure">Religious sites can operate normally. Wear of masks should be elective.</p>
      </div>
    </section>

    <footer class="footer-band">
      <p class="footer-band__call">LETS STOP COVID-19</p>
      <p class="footer-band__motto">STAY
        <svg viewBox="0 0 42 36" aria-hidden="true">
          <polygon points="21,1 41,18 36,18 36,35 6,35 6,18 1,18" fill="var(--red)"/>
          <rect x="17" y="23" width="8" height="12" fill="var(--black)"/>
        </svg>
        STAY SAFE</p>
    </footer>
  </main>
</body>
</html>
```